American cannabis tech company business card design

Pavrel.com is seeking a modern, professional, and brand-aligned business card that represents our company and its core values: Mission, Story, Values, and Impact. As an innovative cannabis company, we want a business card that is not only visually appealing but also serves as a representation of who we are and what we stand for.

Project Scope: Design a double-sided business card that integrates our brand identity and core values. Incorporate our key brand elements, ensuring a sleek and contemporary aesthetic. Visually reflect our core values (Mission, Story, Values, Impact) in a way that is engaging yet professional.

Target Market(s)

Vendors, third parties,

Contact Information for Business Card

Contact details (name, title, email, phone, website, etc.)

Font styles to use
Other font styles liked:
• Caslon, Centra

Colors

Designer to choose colors to be used in the design.

Requirements
Must have
• Pavrel.com logo and branding A creative yet clean way to integrate our core values (Mission, Story, Values, Impact) Modern typography and a well-structured layout
Nice to have
• forest green, grey, white, black
Should not have
• references to marijuana, leafs, plants, or related product

```html
<!DOCTYPE html>
<html lang="en">
<head>
<meta charset="utf-8">
<title>Pavrel.com Business Card</title>
<link rel="stylesheet" href="https://fonts.googleapis.com/css2?family=Poppins:wght@300;400;600;800&display=swap">
<style>
  :root {
    --forest: #1f4a26;
    --forest-deep: #173a1d;
    --paper: #f1f1f1;
    --paper-shade: #e2e2e2;
    --ink: #2b2b2b;
    --backdrop: #dcdad6;
  }
  * { margin: 0; padding: 0; box-sizing: border-box; }
  html, body {
    width: 1200px; height: 917px; overflow: hidden;
    background: var(--backdrop);
    font-family: "Poppins", sans-serif;
  }
  .canvas {
    width: 1200px; height: 917px;
    display: flex; align-items: center; justify-content: center; gap: 50px;
  }
  .card {
    position: relative;
    width: 525px; height: 300px;
    background: linear-gradient(135deg, var(--paper) 0%, var(--paper-shade) 100%);
    box-shadow: 0 6px 18px rgba(0,0,0,0.18);
    overflow: hidden;
  }
  .band {
    position: absolute; left: 0; right: 0;
    background: linear-gradient(90deg, var(--forest-deep), var(--forest));
  }
  /* front */
  .card--front .band { top: 118px; height: 132px; }
  .brand-name {
    font-family: "Poppins", sans-serif;
    font-weight: 800;
    letter-spacing: 0.02em;
    line-height: 1;
  }
  .card--front .brand-name {
    position: absolute; left: 40px; top: 34px;
    font-size: 62px; color: var(--forest);
  }
  .contact {
    position: absolute; left: 40px; bottom: 64px;
    color: #ffffff;
  }
  .contact__name { font-weight: 600; font-size: 17px; letter-spacing: 0.03em; }
  .contact__title { font-weight: 300; font-size: 13px; margin-bottom: 10px; }
  .contact__row {
    display: flex; align-items: center; gap: 8px;
    font-weight: 300; font-size: 12.5px; line-height: 20px;
  }
  .contact__icon {
    width: 15px; height: 15px; border-radius: 3px;
    background: #ffffff; display: flex; align-items: center; justify-content: center;
  }
  .social {
    position: absolute; right: 26px; top: 132px;
    display: flex; gap: 7px;
  }
  .social__mark {
    width: 15px; height: 15px; border-radius: 3px; background: #ffffff;
  }
  /* back */
  .card--back .band { top: 110px; height: 120px; }
  .card--back .brand-name {
    position: absolute; left: 0; right: 0; top: 134px;
    text-align: center; font-size: 72px; color: #ffffff;
  }
  .values {
    position: absolute; left: 0; right: 0; top: 82px;
    text-align: center;
    font-weight: 300; font-size: 12px; letter-spacing: 0.2em;
    color: var(--ink);
  }
</style>
</head>
<body>
<main class="canvas">

  <section class="card card--front" aria-label="Business card front">
    <div class="band"></div>
    <div class="brand-name">PAVREL</div>
    <div class="social" aria-label="Social profiles">
      <span class="social__mark"></span>
      <span class="social__mark"></span>
      <span class="social__mark"></span>
    </div>
    <div class="contact">
      <p class="contact__name">JORDAN L. HALE</p>
      <p class="contact__title">Director</p>
      <p class="contact__row">
        <span class="contact__icon">
          <svg width="11" height="11" viewBox="0 0 24 24"><path fill="#1f4a26" d="M6.6 10.8a15 15 0 0 0 6.6 6.6l2.2-2.2a1 1 0 0 1 1-.25 11.4 11.4 0 0 0 3.6.57 1 1 0 0 1 1 1V20a1 1 0 0 1-1 1A17 17 0 0 1 3 4a1 1 0 0 1 1-1h3.5a1 1 0 0 1 1 1c0 1.25.2 2.45.57 3.57a1 1 0 0 1-.25 1z"/></svg>
        </span>+1 555-014-2283
      </p>
      <p class="contact__row">
        <span class="contact__icon">
          <svg width="11" height="11" viewBox="0 0 24 24"><rect x="2" y="5" width="20" height="14" rx="2" fill="none" stroke="#1f4a26" stroke-width="2.4"/><path d="M3 6l9 7 9-7" fill="none" stroke="#1f4a26" stroke-width="2.4"/></svg>
        </span>team@pavrel.com
      </p>
      <p class="contact__row">
        <span class="contact__icon">
          <svg width="11" height="11" viewBox="0 0 24 24"><circle cx="12" cy="12" r="9.5" fill="none" stroke="#1f4a26" stroke-width="2.2"/><ellipse cx="12" cy="12" rx="4" ry="9.5" fill="none" stroke="#1f4a26" stroke-width="2"/><path d="M3 12h18" stroke="#1f4a26" stroke-width="2"/></svg>
        </span>www.pavrel.com
      </p>
    </div>
  </section>

  <section class="card card--back" aria-label="Business card back">
    <div class="band"></div>
    <p class="values">Mission | Story | Values and Impact</p>
    <div class="brand-name">PAVREL</div>
  </section>

</main>
</body>
</html>
```